Business Card: RW Office Partners - Your organised problem solver

Business Name: RW Office Partners
Website: www.rwofficepartners.com.au
Email: marisol@rwofficepartners.com.au
Mobile: 61 482 907 236
Facebook: @rwofficepartners
Instrgram: @rwofficepartners

Brading Colours:
HEX
#986474
#ddccd3
#7a8498
#c9d8e4
#000000
#ffffff

Tag Line: Your reliable admin partner

Link to DRAFT website:
https://deskhelpcollective.wixsite.com/rw-office-partners

About Page from the website:
My name is Marisol Wrenfield, and I would love to assist you to become more productive in your day to day and achieve your business and personal goals.
My mission is to give you time, time to work on the important tasks of your business or to be able to spend more time with your family. I will take on the tasks you don’t have time for, don’t know well or simply don’t like to do.
I have an extensive background in Administration, Tender Coordination, Document Control, WHS and Quality Management working primarily in the Construction, Mining and Corporate World.
I am passionate about being organised, having order and making things in your life (and mine) easier! I love to watch something unfold and grow into something amazing! I am known for being the go-to problem solver, the organiser of all things, producing high standards of work even under pressure. I’m also a confident communicator, and I understand that you’re busy running your business.

Target Market(s)

Small to Medium Business who require assistance in their business by a virtual assistant.

Industry/Entity Type

Virtual Assistant

Contact Information for Business Card

Mobile: 61 482 907 236

Font styles to use
Sans Serif

Colors
ffffff

Requirements
Must have
• Branding Colours as outlined.
Contact Details as outlined.
Logo as provided.
Proper contact details - mobile, facebook, instragm, website.
Simple, Elegant, very clean looking.
Should not have
• Note cute with pictures.
Not too girly as still want to market to construction companies.

```html
<!DOCTYPE html>
<html lang="en">
<head>
<meta charset="utf-8">
<title>RW Office Partners – Business Card</title>
<link href="https://fonts.googleapis.com/css2?family=Montserrat:wght@500;600&family=Roboto:wght@400;500&display=swap" rel="stylesheet">
<style>
  :root {
    --mauve: #986474;
    --mauve-deep: #7d4f5e;
    --blush: #ddccd3;
    --slate: #7a8498;
    --slate-deep: #565d6c;
    --mist: #c9d8e4;
    --ink: #2a2a2e;
    --paper: #ffffff;
    --backdrop: #e9e6e4;
  }
  * { margin: 0; padding: 0; box-sizing: border-box; }
  html, body {
    width: 1200px; height: 1054px; overflow: hidden;
    background: var(--backdrop);
  }
  .canvas { position: relative; width: 1200px; height: 1054px; }
  .card {
    position: absolute; left: 150px; top: 257px;
    width: 900px; height: 540px;
    background: linear-gradient(160deg, #fbfafa 0%, #f3f0f1 100%);
    border-radius: 22px;
    border: 1px solid #d9d3d5;
    box-shadow: 0 18px 40px rgba(60, 45, 50, 0.12);
    overflow: hidden;
  }
  .brand {
    position: absolute; left: 0; right: 0; top: 92px;
    display: flex; justify-content: center; align-items: center; gap: 22px;
  }
  .brand-mark {
    width: 58px; height: 58px; background: var(--mauve);
  }
  .brand-name {
    font-family: "Montserrat", sans-serif; font-weight: 600;
    font-size: 52px; letter-spacing: 1px; color: var(--slate-deep);
    text-transform: uppercase; white-space: nowrap;
  }
  .person {
    position: absolute; right: 530px; top: 268px; text-align: right;
    white-space: nowrap;
  }
  .person-name {
    font-family: "Montserrat", sans-serif; font-weight: 600;
    font-size: 33px; color: var(--mauve-deep); line-height: 1.1;
  }
  .person-role {
    font-family: "Roboto", sans-serif; font-size: 22px;
    color: var(--ink); margin-top: 8px;
  }
  .divider {
    position: absolute; left: 392px; top: 270px;
    width: 1.5px; height: 100px; background: var(--slate);
  }
  .contacts {
    position: absolute; left: 412px; top: 266px;
    list-style: none; white-space: nowrap;
    font-family: "Roboto", sans-serif; font-size: 22px; color: var(--ink);
  }
  .contacts li { display: flex; align-items: center; gap: 16px; height: 35px; }
  .contacts svg { width: 20px; height: 20px; fill: var(--slate-deep); flex: none; }
  .tagline {
    position: absolute; left: 0; right: 0; top: 408px; height: 46px;
    background: var(--mauve); opacity: 0.92;
    display: flex; align-items: center; justify-content: center;
    font-family: "Montserrat", sans-serif; font-weight: 500;
    font-size: 20px; letter-spacing: 2.5px; word-spacing: 6px;
    color: var(--blush); text-transform: uppercase; white-space: nowrap;
  }
  .socials {
    position: absolute; left: 0; right: 0; top: 484px;
    display: flex; justify-content: center; gap: 28px; white-space: nowrap;
    font-family: "Roboto", sans-serif; font-size: 22px; color: var(--ink);
  }
  .socials span { display: flex; align-items: center; gap: 12px; }
  .social-dot { width: 18px; height: 18px; border-radius: 4px; background: var(--slate-deep); }
</style>
</head>
<body>
<div class="canvas">
  <div class="card">
    <div class="brand">
      <div class="brand-mark"></div>
      <div class="brand-name">RW Office Partners</div>
    </div>

    <div class="person">
      <div class="person-name">Marisol Wrenfield</div>
      <div class="person-role">Virtual Assistant</div>
    </div>
    <div class="divider"></div>

    <ul class="contacts">
      <li>
        <svg viewBox="0 0 24 24" aria-hidden="true"><path d="M6.6 10.8a15.1 15.1 0 0 0 6.6 6.6l2.2-2.2a1 1 0 0 1 1-.25 11.4 11.4 0 0 0 3.6.57 1 1 0 0 1 1 1V20a1 1 0 0 1-1 1A17 17 0 0 1 3 4a1 1 0 0 1 1-1h3.5a1 1 0 0 1 1 1c0 1.250.2 2.45.57 3.57a1 1 0 0 1-.25 1z"/></svg>
        61 482 907 236
      </li>
      <li>
        <svg viewBox="0 0 24 24" aria-hidden="true"><path d="M2 5h20v14H2z M4 7v.4l8 5.2 8-5.2V7z" fill-rule="evenodd"/></svg>
        marisol@rwofficepartners.com.au
      </li>
      <li>
        <svg viewBox="0 0 24 24" aria-hidden="true"><path d="M12 2a10 10 0 1 0 0 20 10 10 0 0 0 0-20zm6.9 6h-2.9a15.6 15.6 0 0 0-1.4-3.6A8 8 0 0 1 18.9 8zM12 4c.8 1.2 1.5 2.5 1.9 4h-3.8c.4-1.5 1.1-2.8 1.9-4zM4.3 14a8 8 0 0 1 0-4h3.3a16 16 0 0 0 0 4zm.8 2h2.9c.3 1.3.8 2.5 1.4 3.6A8 8 0 0 1 5.1 16zM8 8H5.1a8 8 0 0 1 4.3-3.6C8.8 5.5 8.3 6.7 8 8zm4 12c-.8-1.2-1.5-2.5-1.9-4h3.8c-.4 1.5-1.1 2.8-1.900 4zm2.3-6H9.7a14 14 0 0 1 0-4h4.6a14 14 0 0 1 0 4zm.3 5.6c.6-1.1 1.1-2.3 1.4-3.6h2.9a8 8 0 0 1-4.3 3.6zM16.4 14a16 16 0 0 0 0-4h3.3a8 8 0 0 1 0 4z"/></svg>
        www.rwofficepartners.com.au
      </li>
    </ul>

    <div class="tagline">Your reliable admin partner</div>

    <div class="socials">
      <span><i class="social-dot"></i>@rwofficepartners</span>
      <span><i class="social-dot"></i>@rwofficepartners</span>
    </div>
  </div>
</div>
</body>
</html>
```